Company Website for Varnoth Signal, an open source data analytics company focused on relationship and li

I need a company/brand website for our new startup, Varnoth Signal LLC. We are a company focused on using life pattern analysis techniques, looking at relationships and how relationships, attributes, and activity cluster to infer aggregate information about individuals and groups. Our focus is on improving the digital advertising market.

We have a company logo which I will upload shortly.

Target Market(s)

Digital Advertising

Number of Pages Required

3 page

Font styles to use
Sans Serif

Requirements
Must have
• An main page, about us, contact page.
Nice to have
• Varnoth Signal relies on state of the art analytics applied to a the digital marketing space. While it is heavy in science, we also understand the art of influence. The website should have a scientific edge but also a flair that illustrates our focus on applying the hard science and analytics to influencing the behavior of people.

```html
<!DOCTYPE html>
<html lang="en">
<head>
<meta charset="utf-8">
<title>Varnoth Signal</title>
<link href="https://fonts.googleapis.com/css2?family=Montserrat:wght@400;600;700&family=Open+Sans:ital,wght@0,400;0,600;0,700;1,400&display=swap" rel="stylesheet">
<style>
:root{
  --orange:#e8821e;
  --orange-dark:#d9701a;
  --blue:#2f9bd6;
  --ink:#1b1b1b;
  --body:#555;
  --muted:#777;
  --footer:#151515;
  --white:#fff;
  --pie-orange:#f26a3d;
  --pie-blue:#2a6fe0;
  --pie-magenta:#d23fb6;
  --pie-teal:#1fb89a;
  --check:#2b8ed0;
  --line:#d5d5d5;
}
*{box-sizing:border-box;margin:0;padding:0}
html,body{width:1200px;height:3629px;overflow:hidden}
body{font-family:"Open Sans",Arial,sans-serif;color:var(--body);background:var(--white);position:relative}
section,header,footer{position:absolute;left:0;width:1200px}
.abs{position:absolute}
.heading{font-family:"Montserrat",Arial,sans-serif;font-weight:700;color:var(--ink);letter-spacing:.5px}

/* hero */
.hero{top:0;height:603px;overflow:hidden}
.hero-photo{position:absolute;inset:0;background:linear-gradient(160deg,#6b4a3a 0%,#a56a3f 30%,#d79a58 48%,#5a4538 70%,#2c2420 100%)}
.hero-shade{position:absolute;inset:0;background:rgba(0,0,0,.25)}
.brand{position:absolute;left:97px;top:44px;display:flex;align-items:center;gap:12px;color:var(--white);font-family:"Montserrat",Arial,sans-serif;font-weight:700;font-size:30px}
.brand .dot{width:22px;height:22px;border-radius:50%;background:var(--white)}
.nav{position:absolute;left:404px;top:60px;display:flex;gap:33px;font-family:"Montserrat",Arial,sans-serif;font-size:15px;font-weight:600;color:var(--white)}
.nav .active{color:var(--orange)}
.search{position:absolute;left:1088px;top:58px}
.hero-title{position:absolute;top:170px;width:100%;text-align:center;font-family:"Montserrat",Arial,sans-serif;font-weight:700;font-size:96px;color:var(--white);letter-spacing:1px}
.hero-sub{position:absolute;top:296px;width:100%;text-align:center;color:var(--white);font-size:19px;line-height:34px}
.btn-ghost{position:absolute;border:2px solid var(--white);border-radius:31px;color:var(--white);font-family:"Montserrat",Arial,sans-serif;font-weight:700;font-size:15px;display:flex;align-items:center;justify-content:center}
.hero .btn-ghost{left:515px;top:390px;width:170px;height:62px}
.dots{position:absolute;top:524px;left:568px;display:flex;gap:5px}
.dots span{width:14px;height:14px;border-radius:50%;border:2px solid var(--white)}
.dots span.on{background:var(--white)}

/* welcome */
.welcome{top:603px;height:595px}
.welcome .heading{position:absolute;top:100px;width:100%;text-align:center;font-size:34px}
.lead{position:absolute;top:162px;left:220px;width:760px;text-align:center;font-size:14px;line-height:28px;color:var(--muted)}
.feature{position:absolute;top:268px;width:320px;text-align:center}
.feature svg{display:block;margin:0 auto}
.feature h3{font-family:"Open Sans",Arial,sans-serif;font-weight:600;font-size:22px;color:var(--ink);margin-top:26px}
.feature p{font-size:14px;line-height:26px;color:var(--muted);margin-top:10px}

/* analysis */
.analysis{top:1198px;height:564px;background:linear-gradient(120deg,#2f9bd6 0%,#3aa4de 55%,#2a86c4 100%);overflow:hidden}
.video{position:absolute;left:99px;top:121px;width:484px;height:324px;background:linear-gradient(135deg,#cfd9e2,#8fa3b5 55%,#5a6d80)}
.play{position:absolute;left:212px;top:132px}
.analysis-frame{position:absolute;left:515px;top:75px;width:584px;height:411px;border:2px solid rgba(255,255,255,.85)}
.analysis h2{position:absolute;left:112px;top:50px;font-family:"Montserrat",Arial,sans-serif;font-weight:700;font-size:36px;color:var(--white)}
.analysis p{position:absolute;left:112px;top:120px;width:430px;font-size:14px;line-height:25px;color:var(--white)}
.analysis .btn-ghost{left:112px;top:311px;width:150px;height:52px;font-size:14px}

/* why */
.why{top:1762px;height:569px}
.why .heading{position:absolute;left:99px;top:104px;font-size:36px}
.ticks{position:absolute;left:99px;top:174px;list-style:none}
.ticks li{display:flex;align-items:center;gap:12px;font-size:14px;color:var(--body);height:32px}
.btn-orange{position:absolute;left:99px;top:404px;width:150px;height:53px;border:2px solid var(--orange);border-radius:27px;color:var(--orange);font-family:"Montserrat",Arial,sans-serif;font-weight:700;font-size:14px;display:flex;align-items:center;justify-content:center}
.pie{position:absolute;left:650px;top:69px}
.pie text{font-family:"Open Sans",Arial,sans-serif;fill:var(--white)}

/* testimonials */
.testimonials{top:2331px;height:496px;background:linear-gradient(120deg,#e5801c,#ec8d2a 60%,#e17818)}
.testimonials .heading{position:absolute;top:82px;width:100%;text-align:center;font-size:34px;color:var(--white)}
.card{position:absolute;top:210px;width:305px;height:196px;border:2px solid rgba(255,255,255,.9);text-align:center;color:var(--white)}
.avatar{position:absolute;left:50%;top:-42px;margin-left:-42px;width:84px;height:84px;border-radius:50%;border:3px solid var(--white);background:linear-gradient(160deg,#c9b4a0,#8a6f5c)}
.card p{position:absolute;top:62px;left:25px;width:255px;font-style:italic;font-size:13px;line-height:25px}
.card h4{position:absolute;top:142px;width:100%;font-size:18px;font-weight:600}
.arrow{position:absolute;width:44px;height:44px;border-radius:50%;border:2px solid var(--white);display:flex;align-items:center;justify-content:center}

/* partners */
.partners{top:2827px;height:363px}
.partners .heading{position:absolute;top:91px;width:100%;text-align:center;font-size:34px}
.badge{position:absolute;top:183px;width:184px;height:87px;border:1px solid var(--line);display:flex;align-items:center;justify-content:center}
.badge span{width:120px;height:28px;border-radius:4px;background:#c9c9c9}
.partners .arrow{border-color:#999;top:205px}

/* footer */
.site-footer{top:3190px;height:439px;background:var(--footer);color:#cfcfcf}
.site-footer .brand{left:99px;top:78px;font-size:30px}
.about{position:absolute;left:99px;top:188px;width:340px;font-size:13px;line-height:23px;color:#cfcfcf}
.signup{position:absolute;left:99px;top:249px;width:334px;height:41px;display:flex}
.signup .field{flex:1;background:var(--white);color:#666;font-size:13px;padding-left:14px;display:flex;align-items:center}
.signup .go{width:82px;background:var(--orange);color:var(--white);font-weight:700;font-size:13px;display:flex;align-items:center;justify-content:center}
.fcol{position:absolute;top:91px}
.fcol h5{font-family:"Montserrat",Arial,sans-serif;font-size:16px;font-weight:700;color:var(--white);margin-bottom:28px}
.fcol li{list-style:none;font-size:13px;color:#d8d8d8;height:25px}
.contact li{display:flex;gap:12px;height:auto;margin-bottom:22px;line-height:22px}
.rule{position:absolute;left:99px;top:343px;width:1002px;height:1px;background:#333}
.copy{position:absolute;left:99px;top:380px;font-size:12px;color:#bdbdbd}
.social{position:absolute;left:927px;top:372px;display:flex;gap:8px}
.social span{width:38px;height:38px;border-radius:50%;border:2px solid #d0d0d0}
</style>
</head>
<body>

<header class="hero">
  <div class="hero-photo" role="img" aria-label="Crowd at a concert raising hands against a warm sunset sky"></div>
  <div class="hero-shade"></div>
  <div class="brand"><span class="dot"></span>Varnoth Signal</div>
  <nav class="nav">
    <span class="active">HOME</span><span>ABOUT</span><span>PLATFORM</span><span>SOLUTIONS</span><span>RESOURCES</span><span>BLOG</span><span>CONTACT</span>
  </nav>
  <svg class="search" width="18" height="18" viewBox="0 0 18 18"><circle cx="7.5" cy="7.5" r="5.5" fill="none" stroke="#fff" stroke-width="2.4"/><line x1="11.5" y1="11.5" x2="16" y2="16" stroke="#fff" stroke-width="2.6"/></svg>
  <h1 class="hero-title">VARNOTH SIGNAL</h1>
  <p class="hero-sub">We are an open source data analytics company focused<br>on relationship and life behaviors.</p>
  <div class="btn-ghost">GET STARTED</div>
  <div class="dots"><span class="on"></span><span></span><span></span><span></span></div>
</header>

<section class="welcome">
  <h2 class="heading">WELCOME TO VARNOTH SIGNAL</h2>
  <p class="lead">Nam libero tempore, cum soluta nobis est eligendi optio cumque nihil impedit quo minus id quod maxime placeat facere possimus, omnis voluptas assumenda est, omnis dolor repellendus quibusdam et aut officiis</p>
  <div class="feature" style="left:89px">
    <svg width="80" height="64" viewBox="0 0 80 64"><g fill="#e8821e"><rect x="4" y="14" width="58" height="9"/><polygon points="60,4 78,18.5 60,33"/><rect x="18" y="41" width="58" height="9"/><polygon points="20,31 2,45.5 20,60"/></g></svg>
    <h3>Data Integration</h3>
    <p>Temporibus autem quibusdam et aut officiis debitis aut rerum necessitatibus saepe even iet ut et voluptates repudiandae sint</p>
  </div>
  <div class="feature" style="left:440px">
    <svg width="70" height="70" viewBox="0 0 70 70"><circle cx="35" cy="35" r="33" fill="#e8821e"/><circle cx="35" cy="18" r="5" fill="#fff"/><rect x="30" y="28" width="10" height="28" rx="2" fill="#fff"/></svg>
    <h3>Information Delivery</h3>
    <p>Temporibus autem quibusdam et aut officiis debitis aut rerum necessitatibus saepe even iet ut et voluptates repudiandae sint</p>
  </div>
  <div class="feature" style="left:789px">
    <svg width="84" height="66" viewBox="0 0 84 66"><g fill="#e8821e"><rect x="2" y="2" width="4" height="62"/><rect x="2" y="60" width="80" height="4"/><rect x="14" y="32" width="9" height="24"/><rect x="27" y="22" width="9" height="34"/><rect x="40" y="36" width="9" height="20"/><rect x="53" y="14" width="9" height="42"/><rect x="66" y="28" width="9" height="28"/></g></svg>
    <h3>Data Analysis</h3>
    <p>Temporibus autem quibusdam et aut officiis debitis aut rerum necessitatibus saepe even iet ut et voluptates repudiandae sint</p>
  </div>
</section>

<section class="analysis">
  <div class="video" role="img" aria-label="Video still of colleagues reviewing a rising line chart on a whiteboard">
    <svg class="play" width="60" height="60" viewBox="0 0 60 60"><circle cx="30" cy="30" r="29" fill="#222" fill-opacity=".85"/><polygon points="23,17 44,30 23,43" fill="#fff"/></svg>
  </div>
  <div class="analysis-frame">
    <h2>LIFE PATTERN ANALYSIS</h2>
    <p>Nam libero tempore, cum soluta nobis est eligendi optio cumque nihil impedit quo minus id quod maxime placeat facere possimus, omnis voluptas assumenda est, omnis dolor repellendus. Tempori bus autem quibusdam et aut officiis debitis aut rerum necessitatib us saepe eveniet ut et voluptates repudiandae sint et molestianon recusan rum rerum hic tenetur a sapien.</p>
    <div class="btn-ghost">READ MORE</div>
  </div>
</section>

<section class="why">
  <h2 class="heading">WHY VARNOTH SIGNAL?</h2>
  <ul class="ticks">
    <li><svg width="15" height="15" viewBox="0 0 15 15"><circle cx="7.5" cy="7.5" r="7.5" fill="#2b8ed0"/><path d="M4 7.8l2.4 2.3L11 5" stroke="#fff" stroke-width="1.8" fill="none"/></svg>At vero eos et accusamus et iusto odio dignissimos ducimus qui blandi</li>
    <li><svg width="15" height="15" viewBox="0 0 15 15"><circle cx="7.5" cy="7.5" r="7.5" fill="#2b8ed0"/><path d="M4 7.8l2.4 2.3L11 5" stroke="#fff" stroke-width="1.8" fill="none"/></svg>Praesentium voluptatum deleniti atque corrupti quos dolores et quas</li>
    <li><svg width="15" height="15" viewBox="0 0 15 15"><circle cx="7.5" cy="7.5" r="7.5" fill="#2b8ed0"/><path d="M4 7.8l2.4 2.3L11 5" stroke="#fff" stroke-width="1.8" fill="none"/></svg>Molestias excepturi sint occaecati cupiditate non provide imilique sunt</li>
    <li><svg width="15" height="15" viewBox="0 0 15 15"><circle cx="7.5" cy="7.5" r="7.5" fill="#2b8ed0"/><path d="M4 7.8l2.4 2.3L11 5" stroke="#fff" stroke-width="1.8" fill="none"/></svg>In culpa qui officia deserunt mollitia animi, id est laborum et dolorum</li>
    <li><svg width="15" height="15" viewBox="0 0 15 15"><circle cx="7.5" cy="7.5" r="7.5" fill="#2b8ed0"/><path d="M4 7.8l2.4 2.3L11 5" stroke="#fff" stroke-width="1.8" fill="none"/></svg>Et harum quidem rerum facilis est et expedita distinctio empore, cum</li>
    <li><svg width="15" height="15" viewBox="0 0 15 15"><circle cx="7.5" cy="7.5" r="7.5" fill="#2b8ed0"/><path d="M4 7.8l2.4 2.3L11 5" stroke="#fff" stroke-width="1.8" fill="none"/></svg>Soluta nobis est eligendi optio cumque nihil impedit quo minus id quo</li>
  </ul>
  <div class="btn-orange">READ MORE</div>
  <svg class="pie" width="430" height="430" viewBox="-215 -215 430 430">
    <circle r="200" fill="#fff" stroke="#e6e6e6" stroke-width="3"/>
    <path d="M0 0 L-25.1 -178.3 A180 180 0 1 1 -8.8 179.8 Z" fill="var(--pie-orange)"/>
    <path d="M0 0 L-8.8 179.8 A180 180 0 0 1 -112.8 140.3 Z" fill="var(--pie-blue)"/>
    <path d="M0 0 L-112.8 140.3 A180 180 0 0 1 -168.3 -63.9 Z" fill="var(--pie-magenta)"/>
    <path d="M0 0 L-168.3 -63.9 A180 180 0 0 1 -25.1 -178.3 Z" fill="var(--pie-teal)"/>
    <circle r="6" fill="#fff"/>
    <text x="65" y="-111" font-size="28" font-weight="700" text-anchor="middle">53%</text>
    <text x="92" y="-66" font-size="18" text-anchor="middle">LIFESTYLE</text>
    <g font-size="16"><text x="41" y="-30">Smoking</text><text x="41" y="-5">Obesity</text><text x="41" y="20">Stress</text><text x="41" y="45">Nutrition</text><text x="41" y="70">Blood Pressure</text><text x="41" y="95">Alcohol</text><text x="41" y="120">Drug Use</text></g>
    <text x="-85" y="-96" font-size="26" font-weight="700" text-anchor="middle">17%</text>
    <text x="-85" y="-64" font-size="15" text-anchor="middle">ATTRIBUTES</text>
    <text x="-100" y="18" font-size="26" font-weight="700" text-anchor="middle">20%</text>
    <text x="-100" y="50" font-size="15" text-anchor="middle">RELATIONSHIPS</text>
    <text x="-27" y="113" font-size="26" font-weight="700" text-anchor="middle">10%</text>
    <text x="-27" y="146" font-size="15" text-anchor="middle">ACTIVITY</text>
  </svg>
</section>

<section class="testimonials">
  <h2 class="heading">CLIENT TESTIMONIALS</h2>
  <div class="arrow" style="left:24px;top:285px"><svg width="12" height="16" viewBox="0 0 12 16"><path d="M9 2L3 8l6 6" stroke="#fff" stroke-width="2.4" fill="none"/></svg></div>
  <div class="card" style="left:99px"><div class="avatar" role="img" aria-label="Portrait of a client"></div><p>Nam libero tempore, cum soluta nobis est eligendi optio cumque nihil impedit quo minus id quod maxime placea</p><h4>Corinne Vaskell</h4></div>
  <div class="card" style="left:448px"><div class="avatar" role="img" aria-label="Portrait of a client"></div><p>Nam libero tempore, cum soluta nobis est eligendi optio cumque nihil impedit quo minus id quod maxime placea</p><h4>Tessa Morwick</h4></div>
  <div class="card" style="left:796px"><div class="avatar" role="img" aria-label="Portrait of a client"></div><p>Nam libero tempore, cum soluta nobis est eligendi optio cumque nihil impedit quo minus id quod maxime placea</p><h4>Aldo Brenner</h4></div>
  <div class="arrow" style="left:1130px;top:285px"><svg width="12" height="16" viewBox="0 0 12 16"><path d="M3 2l6 6-6 6" stroke="#fff" stroke-width="2.4" fill="none"/></svg></div>
</section>

<section class="partners">
  <h2 class="heading">PARTNERS</h2>
  <div class="arrow" style="left:33px"><svg width="12" height="16" viewBox="0 0 12 16"><path d="M9 2L3 8l6 6" stroke="#999" stroke-width="2" fill="none"/></svg></div>
  <div class="badge" style="left:99px"><span></span></div>
  <div class="badge" style="left:303px"><span></span></div>
  <div class="badge" style="left:508px"><span></span></div>
  <div class="badge" style="left:712px"><span></span></div>
  <div class="badge" style="left:917px"><span></span></div>
  <div class="arrow" style="left:1124px"><svg width="12" height="16" viewBox="0 0 12 16"><path d="M3 2l6 6-6 6" stroke="#999" stroke-width="2" fill="none"/></svg></div>
</section>

<footer class="site-footer">
  <div class="brand"><span class="dot"></span>Varnoth Signal</div>
  <p class="about">Nam libero tempore, cum soluta nobis est eligendi optio cumque nihil impedit quo minus id quo..</p>
  <div class="signup"><div class="field">Email Address</div><div class="go">SIGN UP</div></div>
  <div class="fcol" style="left:486px"><h5>QUICK LINKS</h5><ul><li>Home</li><li>About</li><li>Platform</li><li>Solutions</li><li>Resources</li><li>Blog</li><li>Contact</li></ul></div>
  <div class="fcol" style="left:675px"><h5>LEGAL</h5><ul><li style="height:30px">Complaints procedure</li><li style="height:30px">Terms and conditions</li><li style="height:30px">Privacy policy</li><li style="height:30px">Cookies</li><li style="height:30px">Treating customers fairly</li><li style="height:30px">Site map</li></ul></div>
  <div class="fcol contact" style="left:878px"><h5>GET IN TOUCH</h5><ul>
    <li><svg width="12" height="16" viewBox="0 0 12 16"><path d="M6 0a6 6 0 0 0-6 6c0 4.5 6 10 6 10s6-5.5 6-10a6 6 0 0 0-6-6zm0 8.5A2.5 2.5 0 1 1 6 3.5a2.5 2.5 0 0 1 0 5z" fill="#fff"/></svg><span>42-44 Hollin Lane,<br>Ashcombe, Wessex</span></li>
    <li><svg width="13" height="13" viewBox="0 0 13 13"><path d="M2.5 0l2.5 3-1.5 1.8c.9 1.8 2.4 3.3 4.2 4.2L9.5 7.5l3 2.5-1.5 2.5C5.5 12.5.5 7.5.5 2z" fill="#fff"/></svg><span>1 555 014 2277</span></li>
    <li><svg width="14" height="11" viewBox="0 0 14 11"><rect width="14" height="11" fill="#fff"/><path d="M0 0l7 6 7-6" stroke="#151515" stroke-width="1.4" fill="none"/></svg><span>info@varnothsignal.com</span></li>
  </ul></div>
  <div class="rule"></div>
  <p class="copy">Copyrights © 2018, Varnoth Signal. All rights reserved.</p>
  <div class="social"><span></span><span></span><span></span><span></span></div>
</footer>

</body>
</html>
```